Provide bookkeeping and accounting services to small and growing businesses

We need website and logo design using the name Dornaby as the logo.
The target audience are small companies and startups who need:
1) Simple bookkeeping services
2) Accounting advice that only someone with many years of senior financial experience as a CPA can provide.

The services are provided by two individuals. each of whom specialize in one of the areas.

We want the website to be clean without a lot of visual distraction but don't know how to make a boring subject interesting. We believe our potential clients, small business owners, need to find what they want quickly and easily without a lot of verbiage or distractions.

We've attached a draft of the homepage and have completed the text on most of the other pages.

Target Market(s)

small and early stage growth companies in Palomar Coast

Industry/Entity Type

Accounting

Number of Pages Required

1 page

Font styles to use
Sans Serif

Colors
86cfc6
33b8a4
85cae6

Requirements
Must have
• We need a design for the website homepage that includes the name Dornaby as the logo. Must include a design for the name.
• Must have color in teal or greenish blue.
Nice to have
• White background, clean, clear, uncluttered.
• We would like to use the design in a Theme on a Pagecraft website. Themes Paper Lantern and Quiet Harbour are appealing to us.
Should not have
• Moving pictures

```html
<!DOCTYPE html>
<html lang="en">
<head>
<meta charset="utf-8">
<title>Dornaby Accounting &amp; Bookkeeping</title>
<link href="https://fonts.googleapis.com/css2?family=Libre+Baskerville:wght@400;700&family=Open+Sans:wght@400;600;700&display=swap" rel="stylesheet">
<style>
:root{
  --teal:#33b8a4;
  --teal-soft:#86cfc6;
  --ink:#333333;
  --body:#555555;
  --muted:#999999;
  --footer:#444444;
  --grey-band:#efefef;
  --white:#ffffff;
  --serif:"Libre Baskerville", Georgia, serif;
  --sans:"Open Sans", Arial, sans-serif;
}
*{box-sizing:border-box;margin:0;padding:0}
html,body{width:1200px;height:2679px;overflow:hidden;background:var(--white)}
body{position:relative;font-family:var(--sans);color:var(--body)}

/* header */
.site-header{position:absolute;left:0;top:0;width:1200px;height:121px;border-top:5px solid var(--teal);background:var(--white)}
.brand{position:absolute;left:102px;top:32px}
.brand-name{font-family:var(--serif);font-weight:700;font-size:27px;color:var(--teal);letter-spacing:1px;line-height:1}
.brand-tag{font-size:12.5px;color:var(--ink);margin-top:6px;letter-spacing:.3px}
.main-nav a{position:absolute;top:48px;font-size:14.5px;color:var(--ink);text-decoration:none;letter-spacing:.2px}
.main-nav a.active{color:var(--teal)}
.search-icon{position:absolute;left:1086px;top:52px}

/* hero */
.hero{position:absolute;left:0;top:121px;width:1200px;height:518px;background:linear-gradient(120deg,#c9cfd3 0%,#eef1f2 35%,#f7f8f8 60%,#d8dcd6 100%)}
.hero-caption{position:absolute;left:339px;top:209px;width:523px;height:114px;background:rgba(40,40,40,.85);padding:22px 24px}
.hero-caption h1{font-family:var(--serif);font-weight:700;color:var(--white);font-size:24px;line-height:36px;letter-spacing:.5px}
.hero-arrow{position:absolute;top:353px;width:36px;height:36px;display:flex;align-items:center;justify-content:center}
.hero-arrow.prev{left:339px;background:var(--teal)}
.hero-arrow.next{left:379px;background:#555}

/* welcome */
.welcome{position:absolute;left:0;top:639px;width:1200px;height:290px;text-align:center}
.welcome .eyebrow{position:absolute;top:49px;width:100%;font-size:17px;letter-spacing:1.5px;color:var(--ink)}
.welcome h2{position:absolute;top:79px;width:100%;font-family:var(--serif);font-weight:700;font-size:24px;color:var(--teal);letter-spacing:1px}
.welcome p{position:absolute;left:130px;top:119px;width:940px;font-size:12.5px;line-height:22px;color:var(--body)}
.btn-view{position:absolute;left:555px;top:211px;width:90px;height:33px;background:var(--teal);color:var(--white);font-family:var(--serif);font-weight:700;font-size:11.5px;line-height:33px;letter-spacing:.5px;border-radius:2px}

/* services */
.services{position:absolute;left:0;top:929px;width:1200px;height:459px;background:linear-gradient(180deg,#2f3437,#22272a)}
.services h2{position:absolute;top:50px;width:100%;text-align:center;font-family:var(--serif);font-weight:700;font-size:25px;color:var(--teal);letter-spacing:2px}
.services .sub{position:absolute;top:109px;width:100%;text-align:center;font-size:15px;color:var(--white)}
.service{position:absolute;top:178px;width:220px;text-align:center}
.service .icon{width:158px;height:158px;border-radius:50%;background:var(--teal);margin:0 auto;display:flex;align-items:center;justify-content:center}
.service .label{margin-top:26px;font-size:17px;font-weight:600;color:var(--white);letter-spacing:.3px}

/* about */
.about{position:absolute;left:0;top:1388px;width:1200px;height:353px}
.about h2{position:absolute;left:161px;top:56px;font-family:var(--serif);font-weight:700;font-size:24px;color:var(--teal);letter-spacing:.5px}
.about p{position:absolute;left:161px;top:106px;width:511px;font-size:11.6px;line-height:22px;text-align:justify}
.read-more{position:absolute;left:161px;top:282px;font-size:11.5px;color:var(--teal);letter-spacing:.5px}
.skill{position:absolute;left:782px;width:257px}
.skill .row{display:flex;justify-content:space-between;font-size:12.5px;color:var(--ink)}
.skill .bar{margin-top:8px;height:8px;background:var(--ink);border-radius:4px;overflow:hidden}
.skill .fill{height:100%;background:var(--teal)}

/* cta */
.cta{position:absolute;left:0;top:1741px;width:1200px;height:138px;background:var(--teal)}
.cta .need{position:absolute;left:129px;top:48px;font-size:27px;font-weight:700;color:var(--white)}
.cta .pitch{position:absolute;left:326px;top:48px;font-size:27px;font-weight:600;color:var(--white)}
.btn-quote{position:absolute;left:889px;top:41px;width:142px;height:52px;background:#222;color:var(--white);font-size:16px;font-weight:600;text-align:center;line-height:52px;border-radius:2px}

/* testimonials */
.testimonials{position:absolute;left:0;top:1879px;width:1200px;height:404px}
.testimonials h2{position:absolute;top:63px;width:100%;text-align:center;font-family:var(--serif);font-weight:700;font-size:24px;color:var(--teal);letter-spacing:.5px}
.client-photo{position:absolute;top:121px;width:106px;height:106px;border-radius:50%;border:3px solid #e3e3e3;background:linear-gradient(180deg,#cfd6dc,#6f7a84)}
.quote{position:absolute;top:117px;width:252px;font-size:12px;line-height:22.5px;text-align:justify}
.client-name{position:absolute;top:218px;font-size:15px;color:var(--teal);font-weight:600}
.client-role{position:absolute;top:243px;font-size:11.5px;color:var(--muted)}
.rating{position:absolute;top:269px;display:flex;align-items:center;gap:5px;font-size:10.5px;color:var(--muted)}
.rating .stars{color:#e8b923;font-size:12px;letter-spacing:2px}
.slide-dot{position:absolute;top:2154px;width:37px;height:37px;border-radius:50%;background:#e4e4e4;display:flex;align-items:center;justify-content:center}

/* partners */
.partners{position:absolute;left:0;top:2283px;width:1200px;height:105px;background:var(--grey-band)}
.partner{position:absolute;top:36px;display:flex;align-items:center;gap:9px;font-size:22px;font-weight:600;color:#444}
.partner .mark{width:20px;height:20px;border-radius:50%;background:#555}

/* footer */
.site-footer{position:absolute;left:0;top:2388px;width:1200px;height:241px;background:var(--footer);color:#dddddd}
.footer-col{position:absolute;top:44px}
.footer-col h3{font-size:16px;font-weight:600;color:var(--white);margin-bottom:16px}
.footer-col ul{list-style:none}
.footer-col li{font-size:11px;line-height:26px;color:#dddddd}
.contact-line{font-size:11px;line-height:24px}
.socials{display:flex;gap:14px;margin-top:14px}
.socials span{width:36px;height:36px;border-radius:50%;border:1px solid #ccc;display:flex;align-items:center;justify-content:center}
.socials span i{display:block;width:10px;height:10px;border-radius:50%;background:#ddd}
.newsletter p{font-size:11px;margin-bottom:14px}
.signup{display:flex}
.signup .field{width:175px;height:42px;border:1px solid #777;font-size:11px;line-height:40px;padding-left:14px;color:var(--white)}
.signup .go{width:98px;height:42px;background:var(--teal);color:var(--white);font-size:12px;font-weight:600;line-height:42px;text-align:center}
.copyright{position:absolute;left:0;top:2629px;width:1200px;height:50px;background:var(--teal);color:var(--white);font-size:11.5px;text-align:center;line-height:50px}
</style>
</head>
<body>

<header class="site-header">
  <div class="brand">
    <div class="brand-name">DORNABY</div>
    <div class="brand-tag">ACCOUNTING &amp; BOOKKEEPING</div>
  </div>
  <nav class="main-nav">
    <a class="active" style="left:479px">HOME</a>
    <a style="left:552px">ABOUT US</a>
    <a style="left:654px">SERVICES</a>
    <a style="left:747px">EXPERIENCE</a>
    <a style="left:859px">RESOURCES</a>
    <a style="left:972px">CONTACT US</a>
  </nav>
  <svg class="search-icon" width="16" height="16" viewBox="0 0 16 16"><circle cx="6.5" cy="6.5" r="4.8" fill="none" stroke="#33b8a4" stroke-width="2.2"/><line x1="10" y1="10" x2="14.5" y2="14.5" stroke="#33b8a4" stroke-width="2.4"/></svg>
</header>

<section class="hero" role="img" aria-label="Photo of hands reviewing printed financial charts and reports on a desk">
  <div class="hero-caption"><h1>ADVICE FOR SMALL START UP COMPANIES.</h1></div>
  <div class="hero-arrow prev"><svg width="12" height="16" viewBox="0 0 12 16"><polyline points="9,2 3,8 9,14" fill="none" stroke="#fff" stroke-width="2"/></svg></div>
  <div class="hero-arrow next"><svg width="12" height="16" viewBox="0 0 12 16"><polyline points="3,2 9,8 3,14" fill="none" stroke="#fff" stroke-width="2"/></svg></div>
</section>

<section class="welcome">
  <div class="eyebrow">WELCOME TO</div>
  <h2>DORNABY &nbsp;ACCOUNTING &amp; BOOKKEEPING</h2>
  <p>Dornaby offers a flexible range of accounting and bookkeeping services and support for small and growing organizations in the Palomar Coast region. We provide book-keeping services specializing in LedgerNest® at your offices or remotely from ours. We also provide a broad range of accounting services or financial advice. Dornaby offers a flexible range of accounting and bookkeeping services and support for small and growing organizations in the Palomar Coast region.</p>
  <div class="btn-view">VIEW INFO</div>
</section>

<section class="services">
  <h2>OUR &nbsp;SERVICES</h2>
  <div class="sub">ADVICE FOR SMALL START UP COMPANIES</div>
  <div class="service" style="left:181px">
    <div class="icon"><svg width="74" height="60" viewBox="0 0 74 60" fill="none" stroke="#fff" stroke-width="3"><rect x="6" y="4" width="56" height="13" rx="3"/><rect x="10" y="23" width="56" height="13" rx="3"/><rect x="6" y="42" width="60" height="14" rx="3"/><line x1="14" y1="10" x2="54" y2="10"/><line x1="18" y1="29" x2="58" y2="29"/><line x1="14" y1="49" x2="58" y2="49"/></svg></div>
    <div class="label">BOOK KEEPING</div>
  </div>
  <div class="service" style="left:490px">
    <div class="icon"><svg width="70" height="64" viewBox="0 0 70 64" fill="none" stroke="#fff" stroke-width="3"><rect x="6" y="4" width="58" height="42" rx="2"/><line x1="35" y1="46" x2="35" y2="58"/><line x1="22" y1="60" x2="48" y2="60"/><circle cx="35" cy="25" r="11"/><path d="M35 14 V25 H46"/></svg></div>
    <div class="label">FINANCIAL</div>
  </div>
  <div class="service" style="left:799px">
    <div class="icon"><svg width="76" height="62" viewBox="0 0 76 62"><path d="M28 6 H70 V38 H56 L50 46 L48 38 H28 Z" fill="#fff"/><path d="M6 22 H24 V42 H44 V50 H22 L14 58 L14 50 H6 Z" fill="#fff"/><text x="49" y="31" text-anchor="middle" font-family="Open Sans, sans-serif" font-weight="700" font-size="24" fill="#33b8a4">$</text></svg></div>
    <div class="label">ACCOUNTING</div>
  </div>
</section>

<section class="about">
  <h2>ABOUT US</h2>
  <p>Lorem Ipsum is simply dummy text of the printing and typesetting industry. Lorem Ipsum has been the industry's standard dummy text ever since the 1500s, when an unknown printer took a galley of type and scrambled it to make a type specimen book. It has survived not only five centuries, but also the leap into electronic typesetting, remaining essentially unchanged. It was popularised in the 1960s with the release of Glyphsheet sheets containing Lorem Ipsum passages, and more recently with desktop publishing software like Pressmaker Studio including versions of Lorem Ipsum.</p>
  <div class="read-more">READ MORE &#10230;</div>
  <div class="skill" style="top:82px"><div class="row"><span>Book Keeping Services</span><span>85 %</span></div><div class="bar"><div class="fill" style="width:85%"></div></div></div>
  <div class="skill" style="top:134px"><div class="row"><span>Financial Consulting</span><span>65 %</span></div><div class="bar"><div class="fill" style="width:65%"></div></div></div>
  <div class="skill" style="top:190px"><div class="row"><span>Accounting Consulting</span><span>95 %</span></div><div class="bar"><div class="fill" style="width:95%"></div></div></div>
  <div class="skill" style="top:241px"><div class="row"><span>Problem Solving</span><span>75 %</span></div><div class="bar"><div class="fill" style="width:75%"></div></div></div>
</section>

<section class="cta">
  <div class="need">Need Help ?</div>
  <div class="pitch">Advice for small start up companies</div>
  <div class="btn-quote">Get a quote</div>
</section>

<section class="testimonials">
  <h2>WHAT OUR CLIENTS SAY</h2>
  <div class="client-photo" style="left:166px" role="img" aria-label="Portrait photo of client Marissa Holt"></div>
  <p class="quote" style="left:304px">Lorem Ipsum is simply dummy text of the printing and typesetting industry. Lorem Ipsum has been the industry's standard dummy text ever since the 1500s,</p>
  <div class="client-name" style="left:304px">Marissa Holt,</div>
  <div class="client-role" style="left:304px">Financial Services Professional</div>
  <div class="rating" style="left:304px"><span class="stars">★★★★☆</span><span>◌ comments</span></div>

  <div class="client-photo" style="left:647px" role="img" aria-label="Portrait photo of client Teodora L. Vance"></div>
  <p class="quote" style="left:784px">Lorem Ipsum is simply dummy text of the printing and typesetting industry. Lorem Ipsum has been the industry's standard dummy text ever since the 1500s,</p>
  <div class="client-name" style="left:784px">Teodora L. Vance,</div>
  <div class="client-role" style="left:784px">Financial Services Professional</div>
  <div class="rating" style="left:784px"><span class="stars">★★★★☆</span><span>◌ comments</span></div>
</section>
<div class="slide-dot" style="left:541px"><svg width="10" height="14" viewBox="0 0 10 14"><polyline points="7,2 2,7 7,12" fill="none" stroke="#fff" stroke-width="2"/></svg></div>
<div class="slide-dot" style="left:593px"><svg width="10" height="14" viewBox="0 0 10 14"><polyline points="3,2 8,7 3,12" fill="none" stroke="#fff" stroke-width="2"/></svg></div>

<section class="partners">
  <div class="partner" style="left:112px"><span class="mark"></span>Pagecraft</div>
  <div class="partner" style="left:325px"><span class="mark"></span>Sitewell</div>
  <div class="partner" style="left:536px"><span class="mark"></span>Shopform</div>
  <div class="partner" style="left:746px"><span class="mark"></span>Nodebase</div>
  <div class="partner" style="left:957px"><span class="mark"></span>Scriptly</div>
</section>

<footer class="site-footer">
  <div class="footer-col" style="left:102px">
    <h3>Services</h3>
    <ul>
      <li>›&nbsp;&nbsp;Book Keeping Services</li><li>›&nbsp;&nbsp;Financial</li><li>›&nbsp;&nbsp;Accounting</li><li>›&nbsp;&nbsp;Carpentry</li><li>›&nbsp;&nbsp;Glazing</li>
    </ul>
  </div>
  <div class="footer-col" style="left:314px">
    <h3>Quick Links</h3>
    <ul>
      <li>✓&nbsp;&nbsp;Privacy</li><li>✓&nbsp;&nbsp;Terms</li><li>✓&nbsp;&nbsp;Forms and applications</li><li>✓&nbsp;&nbsp;contact info</li>
    </ul>
  </div>
  <div class="footer-col" style="left:520px">
    <h3>Get in Touch</h3>
    <div class="contact-line">Address : 14 Birchwood Lane, Palomar Coast 92008.</div>
    <div class="contact-line">Phone : 760 555 0142, 760 555 0187</div>
    <div class="contact-line">Email : hello@dornaby-mail.com</div>
    <div class="socials"><span><i></i></span><span><i></i></span><span><i></i></span></div>
  </div>
  <div class="footer-col newsletter" style="left:830px">
    <h3>Sign up to News letter</h3>
    <p>Excepteur sint occaecat cupidatat non proident,</p>
    <div class="signup"><div class="field">Enter Email</div><div class="go">SUBSCRIBE</div></div>
  </div>
</footer>
<div class="copyright">Copyright @ 2016, Dornaby.com All Rights Reserved.</div>

</body>
</html>
```